Tide & Thistle Website Creation For Online Spirits Sales via MerrowVats.com

Want a Website developed that I will use to partner with Merrow Vats to sell my signature rum online. Merrow Vats will add the final code to make the website an e-commerce site. Website should have links to Social media pages, recipies, About, news and events, products. I have he domain name already just need a designer to make the website look professional. Need website capable of being viewed on iPhone and Android devices. Please use the color scheme that is on the label. The brand motto is: Celebrate Life With Family old and new friends. The bottle sent in the images will be replaced with and actual high resolution image of the bottle when it is produce on 27 DEC 21. Can give the selected designer access to develop the website. I have the hostbramble.com domain name. Final code will be added by a designer from MerrowVats.com to make it a e-commerce store.
Updates

I added more information to refine the design I wanted. I should have had this information available to the designers when I started the project.

Target Market(s)

Target Market is 25-50 year old who drink rum

Industry/Entity Type

Spirits. Using Website to sell Rum online

Number of Pages Required

1 page

Font styles to use
Sans Serif

Colors
00AB8E
00BBA5
67D7C9
C6EFE9
E9F9F6

Requirements
Must have
• Must look elegant and of high class. Rum is being market as a premium unnamed rum.
Nice to have
• Video of people drinking, smiling and celebrating

```html
<!DOCTYPE html>
<html lang="en">
<head>
<meta charset="utf-8">
<title>Tide &amp; Thistle</title>
<link rel="stylesheet" href="https://fonts.googleapis.com/css2?family=Cinzel:wght@500;700&family=Lato:wght@400;700&family=Montserrat:wght@500&display=swap">
<style>
:root{
  --teal:#1fa98c;
  --teal-deep:#17957b;
  --teal-light:#5fd0bd;
  --mint:#c6efe9;
  --ink:#1b1b1b;
  --body:#333;
  --white:#fff;
  --footer-bg:#f1f1f1;
  --hero-dark:#1a1410;
}
*{box-sizing:border-box;margin:0;padding:0}
html,body{width:1200px;height:3380px;overflow:hidden}
body{position:relative;font-family:'Lato',sans-serif;color:var(--body);background:var(--white)}
.abs{position:absolute}
.serif{font-family:'Cinzel',serif;font-weight:700}

/* hero */
.hero{left:0;top:0;width:1200px;height:634px;
  background:radial-gradient(ellipse at 78% 45%,#7a4a22 0%,#3b2414 30%,var(--hero-dark) 70%),var(--hero-dark)}
.brand{font-family:'Cinzel',serif;font-weight:500;color:var(--white);font-size:21px;display:flex;flex-direction:column;align-items:center;gap:6px}
.brand .dot{width:42px;height:42px;border-radius:50%;border:2px solid var(--white)}
.nav{left:372px;top:43px;display:flex;gap:48px;font-size:15px;color:var(--white)}
.nav .active{color:var(--teal-light)}
.util{top:47px;display:flex;gap:12px}
.soc-dot{width:12px;height:12px;border-radius:50%;background:currentColor;display:block}
.hero h1{left:113px;top:232px;font-family:'Cinzel',serif;font-weight:700;color:var(--white);font-size:41px;letter-spacing:.5px}
.hero p{left:113px;top:298px;width:580px;color:var(--white);font-size:15px;line-height:24px}
.btn{display:flex;align-items:center;justify-content:center;background:var(--teal);color:var(--white);border-radius:30px}
.hero .btn{left:112px;top:372px;width:176px;height:59px;font-family:'Cinzel',serif;font-weight:700;font-size:15px}

/* about */
.about h2{left:110px;top:800px;font-size:32px;color:var(--ink);font-variant:small-caps;font-family:'Cinzel',serif;font-weight:700}
.underline{left:112px;top:846px;width:90px;height:3px;background:var(--teal)}
.about p{left:114px;top:875px;width:440px;font-size:15px;line-height:25.7px;color:var(--body)}
.about .btn{left:110px;top:1078px;width:138px;height:52px;font-family:'Montserrat',sans-serif;font-size:15px}
.emblem{left:599px;top:723px;width:490px;height:490px;border-radius:50%;
  background:radial-gradient(circle at 50% 50%,#1fae92 0 60%,var(--white) 60% 63%,var(--teal) 63%)}

/* solutions */
.solutions{left:0;top:1304px;width:1200px;height:576px;background:var(--teal)}
.solutions h2{left:0;width:1200px;top:64px;text-align:center;color:var(--white);font-size:34px;font-variant:small-caps}
.sol{top:158px;width:232px;text-align:center;color:var(--white)}
.ring{width:196px;height:196px;margin:0 auto;border-radius:50%;background:var(--teal-light);display:flex;align-items:center;justify-content:center}
.ring span{width:168px;height:168px;border-radius:50%;background:var(--white);display:flex;align-items:center;justify-content:center}
.sol h3{margin-top:26px;font-family:'Cinzel',serif;font-weight:700;font-size:22px;font-variant:small-caps;white-space:nowrap}
.sol p{margin-top:10px;font-size:13.5px;line-height:24px}
.sol a{display:block;margin-top:8px;font-family:'Cinzel',serif;font-weight:700;font-size:13px;color:var(--white);text-decoration:none}

/* blog */
.blog-title{left:0;width:1240px;top:1954px;text-align:center;font-size:34px;color:var(--ink);font-variant:small-caps}
.photo{top:2033px;width:472px;height:352px}
.photo.a{left:112px;background:linear-gradient(135deg,#2c231b,#6a5234 55%,#2a2017)}
.photo.b{left:614px;top:2033px;height:359px;background:radial-gradient(circle at 58% 40%,#c9701f,#5a3418 35%,#1f150f 75%)}
.card{top:2324px;width:355px;height:175px;background:var(--white);box-shadow:0 2px 10px rgba(0,0,0,.15);padding:28px 28px}
.card .cat{font-size:14px;color:var(--teal)}
.card h4{margin-top:10px;font-family:'Cinzel',serif;font-weight:700;font-size:19px;color:var(--ink);font-variant:small-caps}
.card p{margin-top:12px;font-size:14.5px;line-height:24px;color:var(--body)}
.date{top:2304px;width:107px;height:44px;background:var(--teal);color:var(--white);font-size:17px;display:flex;align-items:center;justify-content:center}

/* testimonials */
.testi{left:0;top:2584px;width:1200px;height:439px;background:var(--teal-deep)}
.quote{left:112px;top:81px;width:76px;height:68px;background:var(--white);color:var(--teal);font-family:'Cinzel',serif;font-weight:700;font-size:64px;display:flex;align-items:center;justify-content:center;line-height:1;padding-top:22px}
.testi h2{left:234px;top:100px;font-size:34px;color:var(--white);font-variant:small-caps}
.testi p{left:234px;top:170px;width:740px;color:var(--white);font-size:15px;line-height:29.5px}
.author{left:232px;top:339px;display:flex;align-items:center;gap:16px;color:var(--white);font-family:'Montserrat',sans-serif;font-size:15px}
.author i{display:block;width:42px;height:1px;background:var(--white)}

/* footer */
.footer{left:0;top:3023px;width:1200px;height:357px;background:var(--footer-bg)}
.footer .brand{left:110px;top:96px;color:var(--ink);font-size:38px;gap:10px}
.footer .brand .dot{width:80px;height:80px;border-color:var(--ink);border-width:4px}
.f-head{font-family:'Cinzel',serif;font-weight:700;font-size:18px;color:var(--ink)}
.contact{left:436px;top:88px}
.contact ul{list-style:none;margin-top:16px}
.contact li{display:flex;gap:14px;font-size:14.5px;line-height:23px;margin-bottom:13px;color:var(--ink)}
.contact svg{flex:none;margin-top:4px}
.news{left:743px;top:88px}
.subscribe{margin-top:18px;width:351px;height:52px;border-radius:30px;background:var(--white);display:flex;align-items:center;justify-content:space-between;padding-left:26px;font-size:14.5px;color:#555}
.subscribe b{width:138px;height:52px;border-radius:30px;background:var(--teal);color:var(--white);font-family:'Cinzel',serif;font-size:15px;display:flex;align-items:center;justify-content:center}
.f-social{margin-top:20px;margin-left:6px;display:flex;gap:18px;color:var(--ink)}
.divider{left:110px;top:273px;width:976px;height:1px;background:#d6d6d6}
.copy{left:0;width:1200px;top:306px;text-align:center;font-size:14.5px;color:var(--ink)}
</style>
</head>
<body>

<section class="abs hero" role="img" aria-label="Glasses of rum on a barrel beside a bottle of Tide & Thistle rum">
  <div class="abs brand" style="left:112px;top:10px"><span class="dot"></span>TIDE &amp; THISTLE</div>
  <nav class="abs nav"><span class="active">Home</span><span>Product</span><span>Shop</span><span>Blog</span><span>Contact Us</span></nav>
  <div class="abs util" style="left:866px;color:#fff">
    <svg width="14" height="14" viewBox="0 0 14 14"><circle cx="6" cy="6" r="4.5" fill="none" stroke="#fff" stroke-width="2"/><path d="M9.5 9.5L13 13" stroke="#fff" stroke-width="2"/></svg>
    <svg width="14" height="14" viewBox="0 0 14 14"><path d="M4 5V3.5a3 3 0 016 0V5" fill="none" stroke="#fff" stroke-width="1.6"/><rect x="1.5" y="5" width="11" height="8.5" fill="#fff"/></svg>
  </div>
  <div class="abs util" style="left:996px;color:#fff"><i class="soc-dot"></i><i class="soc-dot"></i><i class="soc-dot"></i><i class="soc-dot"></i></div>
  <h1 class="abs">WELCOME TO TIDE &amp; THISTLE</h1>
  <p class="abs">Lorem ipsum dolor sit amet, consectetur adipiscing elit, sed do eiusmod tempor incididunt ut labore et dolore magna aliqua.</p>
  <a class="abs btn">GET STARTED</a>
</section>

<section class="about">
  <h2 class="abs">About Tide &amp; Thistle</h2>
  <div class="abs underline"></div>
  <p class="abs">Lorem ipsum dolor sit amet, consectetur adipiscing elit, sed do eiusmod tempor incididunt ut labore et dolore magna aliqua. Quis ipsum suspendisse ultrices gravida. Risus commodo viverra maecenas accumsan lacus vel facilisis. Lorem ipsum dolor sit amet, consectetur adipiscing elit, sed do eiusmod tempor incididunt ut labore et dolore magna aliqua. Quis ipsum suspendisse ultrices gravida.</p>
  <a class="abs btn">Learn More</a>
  <div class="abs emblem" role="img" aria-label="Round teal emblem with sugar cane over a green field"></div>
</section>

<section class="abs solutions">
  <h2 class="abs serif">Our Solutions</h2>
  <div class="abs sol" style="left:94px">
    <div class="ring"><span><svg width="90" height="80" viewBox="0 0 90 80"><path d="M8 44L46 6h26v26L34 70z" fill="var(--teal)"/><path d="M18 58L54 22" stroke="#fff" stroke-width="3"/><circle cx="62" cy="16" r="5" fill="#fff"/><path d="M78 14v22L42 72" fill="none" stroke="var(--teal)" stroke-width="5"/></svg></span></div>
    <h3>White-Label</h3>
    <p>Back in 2014, Merrow Vats brought technology and customi-zation into the beverage</p>
    <a>Learn More</a>
  </div>
  <div class="abs sol" style="left:354px">
    <div class="ring"><span><svg width="80" height="80" viewBox="0 0 80 80"><rect x="4" y="6" width="62" height="48" rx="4" fill="none" stroke="var(--teal)" stroke-width="5"/><rect x="4" y="6" width="62" height="10" fill="var(--teal)"/><rect x="12" y="24" width="20" height="12" fill="var(--teal)"/><rect x="12" y="40" width="26" height="5" fill="var(--teal)"/><rect x="38" y="24" width="20" height="5" fill="var(--teal)"/><path d="M44 40h8v16h14v20H40V56z" fill="var(--teal)"/></svg></span></div>
    <h3>Subscriptions</h3>
    <p>Back in 2014, Merrow Vats brought technology and customi-zation into the beverage</p>
    <a>Learn More</a>
  </div>
  <div class="abs sol" style="left:614px">
    <div class="ring"><span><svg width="84" height="80" viewBox="0 0 84 80"><circle cx="34" cy="22" r="14" fill="none" stroke="var(--teal)" stroke-width="6" stroke-dasharray="6 4"/><rect x="8" y="58" width="10" height="14" fill="var(--teal)"/><rect x="24" y="50" width="10" height="22" fill="var(--teal)"/><rect x="40" y="42" width="10" height="30" fill="var(--teal)"/><rect x="56" y="30" width="12" height="42" fill="var(--teal)"/><path d="M8 50L60 14" stroke="var(--teal)" stroke-width="4"/><path d="M56 8l12 2-4 12z" fill="var(--teal)"/><rect x="2" y="74" width="78" height="4" fill="var(--teal)"/></svg></span></div>
    <h3>Analytics Suite</h3>
    <p>Back in 2014, Merrow Vats brought technology and customi-zation into the beverage</p>
    <a>Learn More</a>
  </div>
  <div class="abs sol" style="left:874px">
    <div class="ring"><span><svg width="86" height="80" viewBox="0 0 86 80"><rect x="2" y="2" width="82" height="44" rx="8" fill="var(--teal)"/><text x="43" y="36" text-anchor="middle" font-family="Montserrat,sans-serif" font-weight="500" font-size="28" fill="#fff">ADS</text><path d="M36 46l-8 12 14-12z" fill="var(--teal)"/><path d="M6 60h8l14-8v26l-14-8H6z" fill="var(--teal)"/></svg></span></div>
    <h3>Direct Marketing</h3>
    <p>Back in 2014, Merrow Vats brought technology and customi-zation into the beverage</p>
    <a>Learn More</a>
  </div>
</section>

<section class="blog">
  <h2 class="abs serif blog-title">Latest Blog</h2>
  <div class="abs photo a" role="img" aria-label="Two glasses of rum beside sugar cane on a wooden table"></div>
  <div class="abs photo b" role="img" aria-label="Glass of amber rum resting on a barrel"></div>
  <article class="abs card" style="left:152px"><div class="cat">Lorem Ipsum</div><h4>Lorem ipsum dolor sit</h4><p>Lorem ipsum dolor sit amet, consectetur adipiscing elit, sed do eiusmod</p></article>
  <div class="abs date" style="left:373px">09/10/201</div>
  <article class="abs card" style="left:654px"><div class="cat">Lorem Ipsum</div><h4>Lorem ipsum dolor sit</h4><p>Lorem ipsum dolor sit amet, consectetur adipiscing elit, sed do eiusmod</p></article>
  <div class="abs date" style="left:875px">09/10/201</div>
</section>

<section class="abs testi">
  <div class="abs quote">&ldquo;</div>
  <h2 class="abs serif">Testimonials</h2>
  <p class="abs">Lorem ipsum dolor sit amet, consectetur adipiscing elit, sed do eiusmod tempor incididunt ut labore et dolore magna aliqua. Quis ipsum suspendisse ultrices gravida. Risus commodo Lorem ipsum dolor sit amet, consectetur adipiscing elit, sed do eiusmod tempor incididunt ut labore et dolore magna aliqua. Quis ipsum suspendisse ultrices gravida. Risus commodo Lorem ipsum dolor sit amet, consectetur adipiscing elit, sed do eiusmod tempor incididunt ut labore et dolore magna</p>
  <div class="abs author"><i></i>Maren Holloway,&nbsp; Lorem Ipsum</div>
</section>

<footer class="abs footer">
  <div class="abs brand"><span class="dot"></span>TIDE &amp; THISTLE</div>
  <div class="abs contact">
    <div class="f-head">CONTACT US</div>
    <ul>
      <li><svg width="12" height="14" viewBox="0 0 12 14"><path d="M6 14S1 8 1 5a5 5 0 0110 0c0 3-5 9-5 9z" fill="var(--teal)"/><circle cx="6" cy="5" r="2" fill="#fff"/></svg><span>Lorem ipsum dolor sit amet,<br>consectetur adipiscing elit, sed</span></li>
      <li><svg width="13" height="13" viewBox="0 0 13 13"><path d="M2 1l3 0 1 3-2 1.5a7 7 0 003.5 3.5L9 7l3 1v3c0 1-1 1.5-2 1.5A10 10 0 01.5 3C.5 2 1 1 2 1z" fill="var(--teal)"/></svg><span>1 (833) 555-0148</span></li>
      <li><svg width="14" height="11" viewBox="0 0 14 11"><rect width="14" height="11" rx="1" fill="var(--teal)"/><path d="M0 1l7 5 7-5" fill="none" stroke="#fff" stroke-width="1.2"/></svg><span>info@companyname.com</span></li>
    </ul>
  </div>
  <div class="abs news">
    <div class="f-head">SUBSCRIBE TO OUR NEWSLETTER</div>
    <div class="subscribe">Enter Your Email<b>SUBSCRIBE</b></div>
    <div class="f-social"><i class="soc-dot"></i><i class="soc-dot"></i><i class="soc-dot"></i><i class="soc-dot"></i></div>
  </div>
  <div class="abs divider"></div>
  <div class="abs copy">© Copyrights 2021 Company Name &nbsp;|&nbsp;&nbsp; All Rights Reserved</div>
</footer>

</body>
</html>
```